Business Card Design

We would like to re-design our business cards. Our Company - Qwinrel Turbochargers, rebuilds turbochargers and sells replacement parts. Our website is: http://www.qwinrelturbochargers-example.com
We just had our logo changed. I will attach the file. Looking for fresh new/modern business card. We like the colors red, black, white and silver. Black background looks attractive, but not a requirement. The final design should communicate reasonable/competitive prices, top quality and reliability of our products.
Updates
Project Deadline Extended
Reason: Need to finalize the info on the card. Currently working on changing address and email info. Want to make sure it is the correct one before accepting the final design. Unless, this is something that can be changed at a later time..??
Industry/Entity Type
Business
Contact Information for Business Card
QWINREL TURBOCHARGERS, LLC
20473 Harwick Lane NE
Massillon, OH 44647
Tel: +1-555-214-7390
Fax: +1-555-267-1842
info@QwinrelTurbochargers-example.com
Our current business card had the following highlights:
*We rebuild all Turbocharges for Automotive, Diesel and Industrial
*Precision Balancing and in-house turbocharger needs
*All Turbocharger replacement parts are made in USA / U.K.
Look and feel
Each slider illustrates characteristics of the customer's brand and the style your logo design should communicate.

```html
<!DOCTYPE html>
<html lang="en">
<head>
<meta charset="utf-8">
<title>Qwinrel Turbochargers – Business Card</title>
<link rel="stylesheet" href="https://fonts.googleapis.com/css2?family=Montserrat:wght@400;500;700;800&display=swap">
<style>
  :root {
    --bg: #d9d9d9;
    --card: #ffffff;
    --ink: #1a1a1a;
    --text: #3a3a3a;
    --red: #e0231c;
    --black: #111111;
    --faint: #f1f1f1;
  }
  * { box-sizing: border-box; margin: 0; padding: 0; }
  html, body {
    width: 1200px; height: 852px; overflow: hidden;
    background: var(--bg);
    font-family: "Montserrat", Arial, sans-serif;
  }
  .stage { position: relative; width: 1200px; height: 852px; }
  .card {
    position: absolute; top: 283px;
    width: 500px; height: 286px;
    background: var(--card);
    border-radius: 18px;
    overflow: hidden;
    box-shadow: 0 6px 18px rgba(0,0,0,.22);
  }
  .card--front { left: 70px; }
  .card--back { left: 630px; }

  .backdrop-art {
    position: absolute;
    border-radius: 50%;
    background: radial-gradient(circle, #f3f3f3 0%, #f7f7f7 55%, rgba(255,255,255,0) 72%);
  }
  .card--front .backdrop-art { right: -40px; top: -30px; width: 300px; height: 300px; }
  .card--back .backdrop-art { right: 10px; top: 20px; width: 260px; height: 260px; }

  .brand {
    position: absolute;
    display: flex; align-items: center; gap: 12px;
  }
  .brand__mark { width: 26px; height: 26px; background: var(--red); }
  .brand__name {
    font-weight: 800; color: var(--ink);
    font-size: 26px; line-height: 1.05; letter-spacing: -.3px;
  }
  .card--front .brand { left: 70px; top: 104px; }

  .front__url {
    position: absolute; left: 0; right: 0; top: 206px;
    text-align: center; font-size: 13px; color: var(--text); font-weight: 500;
  }
  .rule { position: absolute; height: 2px; background: var(--red); }
  .rule--top { right: 24px; top: 60px; width: 80px; }
  .rule--bottom { left: 24px; top: 254px; width: 80px; }

  .back__band {
    position: absolute; left: 0; top: 0; bottom: 0; width: 34px;
    background: var(--black);
    border-right: 4px solid var(--red);
  }
  .card--back .brand { left: 70px; top: 40px; }
  .card--back .brand__name { font-size: 22px; }
  .card--back .brand__mark { width: 22px; height: 22px; }

  .person { position: absolute; right: 34px; top: 118px; text-align: right; }
  .person__name { color: var(--red); font-weight: 700; font-size: 16px; }
  .person__title { color: var(--text); font-size: 11px; margin-top: 2px; }

  .contact {
    position: absolute; left: 70px; top: 170px;
    font-size: 11.5px; color: var(--text); line-height: 1.55; list-style: none;
  }
  .contact__address { margin-bottom: 4px; }
  .contact li { display: flex; align-items: center; gap: 7px; }
  .contact svg { width: 11px; height: 11px; fill: var(--red); flex: none; }
</style>
</head>
<body>
<main class="stage">

  <section class="card card--front" aria-label="Card front">
    <div class="backdrop-art" role="img" aria-label="Faint turbocharger illustration"></div>
    <div class="rule rule--top"></div>
    <div class="brand">
      <span class="brand__mark"></span>
      <span class="brand__name">Qwinrel<br>Turbochargers</span>
    </div>
    <p class="front__url">www.QwinrelTurbochargers-example.com</p>
    <div class="rule rule--bottom"></div>
  </section>

  <section class="card card--back" aria-label="Card back">
    <div class="backdrop-art" role="img" aria-label="Faint turbocharger illustration"></div>
    <div class="back__band"></div>
    <div class="brand">
      <span class="brand__mark"></span>
      <span class="brand__name">Qwinrel<br>Turbochargers</span>
    </div>
    <div class="person">
      <p class="person__name">Your Long Name</p>
      <p class="person__title">Title</p>
    </div>
    <ul class="contact">
      <li class="contact__address">5192 Corwin Ave. NW<br>Eastbrook Falls, Ohio</li>
      <li>
        <svg viewBox="0 0 24 24" aria-hidden="true"><path d="M6.6 10.8a15 15 0 0 0 6.6 6.6l2.2-2.2a1 1 0 0 1 1-.25 11.4 11.4 0 0 0 3.6.57 1 1 0 0 1 1 1V20a1 1 0 0 1-1 1A17 17 0 0 1 3 4a1 1 0 0 1 1-1h3.5a1 1 0 0 1 1 1c0 1.25.2 2.45.57 3.57a1 1 0 0 1-.25 1z"/></svg>
        1.555.214.7390
      </li>
      <li>
        <svg viewBox="0 0 24 24" aria-hidden="true"><path d="M2 5h20v14H2zm2 2v.5l8 5 8-5V7l-8 5z"/></svg>
        info@QwinrelTurbochargers-example.com
      </li>
      <li>
        <svg viewBox="0 0 24 24" aria-hidden="true"><circle cx="12" cy="12" r="10"/></svg>
        www.QwinrelTurbochargers-example.com
      </li>
    </ul>
  </section>

</main>
</body>
</html>
```